Flyer for the Radiant Harvest Worship Day

I am looking to create a flyer for a one day prayer retreat our church is organizing.
This flyer will be posted on social media, websites and will also be printed so it can be mailed to people.
I am looking for something professional, with good use of our logo and band colors (logo colors).
I am counting on the designer's skill, creativity, art and knowledge of media communication to produce a flyer that will effectively and quickly convey the message we are trying to spread.
CONTENT OF THE FLYER:
Event title: Radiant Harvest Worship Day
Date: Tuesday July 2nd, 2019
Time: 11:00AM - 7:00PM
Belmora Hotel, 4875 Wexley Avenue, Portland, Maine 04102 (Room: Juniper)
Event Key words to highlight what the event is about: Prayer, Sharing the Word, Panel discussion, prophecy, Impartation.
Key phrases:
A one day prayer retreat.
Jesus Chris is Lord
Contact info:
www.tolvex.org
Phone: 207 555 3184
Email: contact@brookhavenfold.org

```html
<!DOCTYPE html>
<html lang="en">
<head>
<meta charset="utf-8">
<title>Radiant Harvest Worship Day</title>
<link rel="stylesheet" href="https://fonts.googleapis.com/css2?family=Lato:wght@300;400;700&display=swap">
<style>
  :root {
    --page: #ffffff;
    --frame: #6e6e6e;
    --ink-dark: #3a3937;
    --photo-glow: #f2efc6;
    --photo-light: #d9d6a4;
    --photo-mid: #8a8763;
    --photo-deep: #4b4a42;
    --photo-shadow: #2f2e2a;
    --text-light: #ffffff;
    --text-soft: #d8d6cc;
    --accent-cream: #f4f0b8;
    --brand-navy: #1d3557;
    --brand-flame: #f08a1c;
  }
  * { margin: 0; padding: 0; box-sizing: border-box; }
  html, body {
    width: 882px; height: 1200px; overflow: hidden;
    background: var(--page);
    font-family: "Lato", "Helvetica Neue", Arial, sans-serif;
  }
  .flyer {
    position: absolute; left: 51px; top: 48px;
    width: 748px; height: 1059px;
    background: var(--ink-dark);
    border: 1px solid var(--frame);
    overflow: hidden;
  }
  .hero-photo {
    position: absolute; left: 0; top: 0; width: 100%; height: 720px;
    background:
      radial-gradient(ellipse 45% 30% at 62% 22%, rgba(242,239,198,0.95), rgba(242,239,198,0) 75%),
      radial-gradient(ellipse 40% 55% at 8% 45%, rgba(47,46,42,0.55), rgba(47,46,42,0) 70%),
      radial-gradient(ellipse 30% 40% at 50% 62%, rgba(47,46,42,0.6), rgba(47,46,42,0) 70%),
      radial-gradient(ellipse 70% 25% at 50% 90%, rgba(47,46,42,0.85), rgba(47,46,42,0) 80%),
      linear-gradient(180deg, var(--photo-mid) 0%, var(--photo-light) 25%, #b4b188 45%, var(--photo-mid) 62%, var(--photo-deep) 85%, var(--ink-dark) 100%);
  }
  .brand {
    position: absolute; right: 30px; top: 86px;
    display: flex; align-items: center; gap: 10px;
  }
  .brand-dot { width: 20px; height: 20px; border-radius: 50%; background: var(--brand-flame); }
  .brand-name {
    font-size: 50px; font-weight: 400; color: var(--brand-navy);
    letter-spacing: 1px; line-height: 1;
  }
  .keywords {
    position: absolute; left: 0; top: 448px; width: 100%;
    text-align: center; color: var(--text-light);
    font-weight: 400; font-size: 15px; letter-spacing: 2px;
    text-transform: uppercase; opacity: 0.92;
  }
  .event-title {
    position: absolute; left: 0; top: 486px; width: 100%;
    text-align: center; color: var(--text-light);
    font-weight: 300; font-size: 66px; line-height: 86px;
    text-transform: uppercase;
  }
  .details {
    position: absolute; left: 67px; top: 682px;
    width: 615px; height: 202px;
    border: 2px dashed rgba(255,255,255,0.85);
    border-radius: 32px;
    color: var(--text-light);
    font-weight: 300; font-size: 26px; line-height: 40px;
    text-align: center; padding-top: 20px;
  }
  .details p { display: flex; justify-content: center; align-items: center; gap: 8px; }
  .details svg { width: 22px; height: 22px; flex: none; }
  .tagline {
    position: absolute; left: 0; top: 902px; width: 100%;
    text-align: center; color: var(--text-light);
    font-weight: 300; font-size: 27px;
  }
  .declaration {
    position: absolute; left: 0; top: 944px; width: 100%;
    display: flex; justify-content: center; align-items: center; gap: 12px;
    color: var(--accent-cream); font-weight: 300; font-size: 42px; line-height: 1;
  }
  .declaration .rule { width: 90px; height: 2px; background: var(--accent-cream); }
  .contact {
    position: absolute; left: 0; top: 1014px; width: 100%;
    display: flex; justify-content: center; gap: 22px;
    color: var(--text-soft); font-weight: 400; font-size: 16px;
  }
</style>
</head>
<body>
  <main class="flyer">
    <div class="hero-photo" role="img" aria-label="Photo of a worshipper with raised arms before three crosses against a bright cloudy sky, crowd hands below"></div>

    <div class="brand">
      <span class="brand-dot"></span>
      <span class="brand-name">TOLVEX</span>
    </div>

    <p class="keywords">Prayer · Sharing the Word · Panel Discussion · Prophecy · Impartation</p>

    <h1 class="event-title">Radiant Harvest<br>Worship Day</h1>

    <section class="details">
      <p>
        <svg viewBox="0 0 22 22" fill="none" stroke="#fff" stroke-width="1.3"><rect x="2" y="4" width="18" height="16"/><line x1="2" y1="8" x2="20" y2="8"/><line x1="6" y1="2" x2="6" y2="6"/><line x1="16" y1="2" x2="16" y2="6"/><path d="M5 11h12M5 14h12M5 17h12M8 11v7M11 11v7M14 11v7"/></svg>
        Date: Tuesday July 2nd, 2019
      </p>
      <p>
        <svg viewBox="0 0 22 22" fill="none" stroke="#fff" stroke-width="1.3"><circle cx="11" cy="12" r="8"/><path d="M11 7v5l3 2M4 4l3-2M18 4l-3-2"/></svg>
        Time: 11:00AM - 7:00PM
      </p>
      <p>
        <svg viewBox="0 0 22 22" fill="none" stroke="#fff" stroke-width="1.3"><path d="M11 20s-6-6.5-6-11a6 6 0 0 1 12 0c0 4.5-6 11-6 11z"/><circle cx="11" cy="9" r="2.2"/></svg>
        Belmora Hotel, 4875 Wexley Avenue,
      </p>
      <p>Portland, Maine 04102 (Room: Juniper)</p>
    </section>

    <p class="tagline">A one day prayer retreat.</p>
    <p class="declaration"><span class="rule"></span>Jesus Chris is Lord<span class="rule"></span></p>

    <footer class="contact">
      <span>www.tolvex.org</span>
      <span>Phone: 207 555 3184</span>
      <span>contact@brookhavenfold.org</span>
    </footer>
  </main>
</body>
</html>
```